Veldmark Supplies Business Card

Professional business card that stand out to our potential customers. Front and back with clean modern design

Industry/Entity Type

Oil and gas

Contact Information for Business Card

Name, address, website , office phone and cell number

Requirements
Must have
• Editable files for each employee

```html
<!DOCTYPE html>
<html lang="en">
<head>
<meta charset="utf-8">
<title>Veldmark Supplies Business Card</title>
<link rel="stylesheet" href="https://fonts.googleapis.com/css2?family=Poppins:wght@300;400;500;700&display=swap">
<style>
  :root {
    --page-bg: #e3e6e8;
    --card-bg: #ffffff;
    --brand-red: #e82626;
    --brand-cyan: #13b0d3;
    --ink: #1e1e1e;
  }
  * { margin: 0; padding: 0; box-sizing: border-box; }
  html, body {
    width: 1200px; height: 960px; overflow: hidden;
    background: var(--page-bg);
    font-family: "Poppins", sans-serif;
  }
  .card {
    position: absolute;
    left: 252px;
    width: 699px; height: 399px;
    background: var(--card-bg);
    border-radius: 30px;
    border-left: 4px solid var(--brand-cyan);
    border-bottom: 4px solid var(--brand-cyan);
    overflow: hidden;
  }
  .card--front { top: 60px; }
  .card--back { top: 500px; }

  .wordmark {
    display: flex; align-items: center; gap: 14px;
    color: var(--brand-red);
    font-weight: 700;
    text-transform: uppercase;
    letter-spacing: 1px;
    white-space: nowrap;
  }
  .wordmark__square { background: var(--brand-red); flex: none; }

  .card--front .wordmark {
    position: absolute; left: 50%; top: 50%;
    transform: translate(-50%, -50%);
    font-size: 38px;
  }
  .card--front .wordmark__square { width: 34px; height: 34px; }

  .card--back .wordmark {
    position: absolute; left: 20px; top: 150px;
    font-size: 21px; gap: 10px;
  }
  .card--back .wordmark__square { width: 20px; height: 20px; }

  .address {
    position: absolute; left: 20px; top: 208px;
    color: var(--brand-cyan);
    font-size: 18px; line-height: 24px; font-weight: 400;
    letter-spacing: 0.4px;
  }
  .contacts {
    position: absolute; left: 20px; top: 282px;
    list-style: none;
  }
  .contacts li {
    display: flex; align-items: center; gap: 10px;
    height: 23px;
    font-size: 18px; color: var(--ink); letter-spacing: 0.2px;
  }
  .contacts svg { width: 16px; height: 16px; flex: none; }

  .person {
    position: absolute; right: 27px; top: 168px;
    text-align: right;
  }
  .person__name {
    font-size: 35px; line-height: 40px; white-space: nowrap;
  }
  .person__first { color: var(--brand-red); font-weight: 700; }
  .person__last { color: var(--brand-cyan); font-weight: 300; }
  .person__title {
    font-size: 18px; color: var(--ink); font-weight: 400; margin-top: 2px;
  }
  .accent-bar {
    position: absolute; right: 0; top: 169px;
    width: 19px; height: 62px;
    background: var(--brand-cyan);
  }
</style>
</head>
<body>

<section class="card card--front">
  <div class="wordmark"><span class="wordmark__square"></span>Veldmark Supplies</div>
</section>

<section class="card card--back">
  <div class="wordmark"><span class="wordmark__square"></span>Veldmark Supplies</div>

  <p class="address">48 Alderbrook Lane,<br>Cedarfield, WI 53590</p>

  <ul class="contacts">
    <li>
      <svg viewBox="0 0 16 16" aria-hidden="true"><path fill="var(--brand-red)" d="M3.2 1.5l2.3-.3 1.2 3-1.4 1.1c.8 1.7 2 2.9 3.6 3.7l1.1-1.4 3 1.2-.3 2.3c-.1.8-.8 1.3-1.6 1.2C6.3 11.8 2.4 7.9 2 3.1c0-.8.4-1.5 1.2-1.6z"/></svg>
      (817) 555-0143
    </li>
    <li>
      <svg viewBox="0 0 16 16" aria-hidden="true"><rect x="3.5" y="0.8" width="9" height="14.4" rx="1.6" fill="none" stroke="var(--brand-cyan)" stroke-width="1.4"/><rect x="6" y="5" width="4" height="5" fill="var(--brand-cyan)"/></svg>
      (555) 555-0188
    </li>
    <li>
      <svg viewBox="0 0 16 16" aria-hidden="true"><circle cx="8" cy="8" r="7.3" fill="var(--brand-red)"/><path d="M8 .7v14.6M.7 8h14.6M3 3.5c3 1.6 7 1.6 10 0M3 12.5c3-1.6 7-1.6 10 0" stroke="#fff" stroke-width="1" fill="none"/></svg>
      www.veldmark.example
    </li>
    <li>
      <svg viewBox="0 0 16 16" aria-hidden="true"><rect x="1" y="4" width="14" height="10" rx="1" fill="var(--brand-cyan)"/><path d="M1.5 4.5L8 10l6.5-5.5" stroke="#fff" stroke-width="1.2" fill="none"/></svg>
      info@veldmark.example
    </li>
  </ul>

  <div class="person">
    <p class="person__name"><span class="person__first">Marta</span> <span class="person__last">Kovalen</span></p>
    <p class="person__title">Co-Founder &amp; CEO</p>
  </div>
  <div class="accent-bar"></div>
</section>

</body>
</html>
```